Food Hall in San Clemente, CA by the Pacific Ocean that has 15 vendors and 2 bars

We need a web page design that highlights our food hall in San Clemente, CA. The name of the food hall is Calloway Food Hall. Inside of the food hall there are 15 different vendors and 2 bars. The place has a beautiful patio and it is by Pacific Ocean. Most of the vendors are local to San Clemente area. The highly anticipated location is opening during the summer of 2025. Website should have a dropdown menu for the different vendors that are in the food hall and people should be able to click to their respective business website. The website should also include link to our social media channels and also a link to provide comments and subscribe for the mailing list.
Target Market(s)
Mostly residents in the San Clemente, CA and surrounding areas. Couples, families and tourist alike that are looking for an exceptional dining experience that everyone can find something they like.
Industry/Entity Type
Restaurants
Coding
Number of Pages Required
Font styles to use
Look and feel

```html
<!DOCTYPE html>
<html lang="en">
<head>
<meta charset="utf-8">
<title>Calloway Food Hall — San Clemente</title>
<link href="https://fonts.googleapis.com/css2?family=Lexend:wght@300;400;500;600&display=swap" rel="stylesheet">
<style>
:root{
  --blue:#0a56b0;
  --sky:#1b9bd7;
  --navy:#0d3f8a;
  --ink:#1d1d1f;
  --muted:#6b6f76;
  --mist:#eef2f8;
  --dark:#111214;
  --white:#ffffff;
}
*{margin:0;padding:0;box-sizing:border-box}
html,body{width:1200px;height:3924px;overflow:hidden}
body{position:relative;font-family:'Lexend',sans-serif;color:var(--ink);background:var(--white)}
.abs{position:absolute}
.pill{position:absolute;display:flex;align-items:center;justify-content:center;border-radius:30px;font-size:13px;font-weight:500;text-transform:uppercase;text-decoration:none}
.pill.solid{background:var(--blue);color:var(--white)}
.pill.sky{background:var(--sky);color:var(--white)}
.pill.line{border:1.5px solid var(--blue);color:var(--navy);background:var(--white);font-size:11.5px}
.photo{position:absolute;border-radius:14px}
h2.section-title{position:absolute;font-size:28px;font-weight:600;color:var(--navy);text-transform:uppercase;letter-spacing:-.3px}
h2.section-title span{color:var(--sky)}
.body-copy{font-size:14px;line-height:32.5px;color:var(--ink)}

/* header */
.topbar{left:0;top:0;width:1200px;height:67px;background:#f2f3f5}
.brand{left:104px;top:2px;width:146px;height:146px;border-radius:50%;background:var(--white);box-shadow:0 2px 10px rgba(0,0,0,.25);display:flex;align-items:center;justify-content:center;text-align:center;z-index:3}
.brand span{font-size:17px;font-weight:600;color:var(--navy);line-height:22px;text-transform:uppercase;width:110px}
.nav a{position:absolute;top:27px;font-size:12px;color:#5a5e66;text-decoration:none;text-transform:uppercase}
.nav a.active{color:var(--sky)}
.hero{left:0;top:67px;width:1200px;height:503px;background:linear-gradient(90deg,#0b0c0e 0%,#1c1d20 35%,#5a5f66 60%,#8b8478 80%,#6e6a63 100%)}
.hero-kicker{left:111px;top:194px;font-size:14px;color:var(--white);text-transform:uppercase}
.hero-title{left:111px;top:236px;font-size:28px;font-weight:600;color:var(--sky);line-height:48px;text-transform:uppercase;letter-spacing:-.4px}
.hero-copy{left:111px;top:340px;width:440px;font-size:14px;line-height:32.5px;color:var(--white)}

/* about */
.about{left:0;top:570px;width:1200px;height:668px;background:var(--mist)}

/* vendors */
.vendor-card{position:absolute;top:1407px;width:312px;height:431px;border-radius:10px;background:var(--white);box-shadow:0 0 6px rgba(0,0,0,.12);text-align:center}
.vendor-card .img{position:absolute;left:9px;top:9px;width:294px;height:200px;border-radius:8px}
.vendor-card h3{position:absolute;left:0;width:100%;top:237px;font-size:16px;font-weight:500;color:var(--navy);text-transform:uppercase}
.vendor-card p{position:absolute;left:30px;width:252px;top:274px;font-size:14px;line-height:32.5px}
.vendor-card .pill{left:96px;top:361px;width:120px;height:34px}
.vendor-card.featured{background:var(--blue)}
.vendor-card.featured h3{color:var(--sky)}
.vendor-card.featured p{color:var(--white)}
.vendor-card.featured .pill{background:var(--blue);border-color:var(--white);color:var(--white)}

/* become vendor */
.become{left:0;top:1922px;width:1200px;height:842px;background:var(--mist)}
.perks{left:111px;top:2194px;list-style:none;font-size:14px}
.perks li{position:relative;padding-left:51px;height:37px;line-height:26px}
.perks li::before{content:"";position:absolute;left:33px;top:11px;width:5px;height:5px;border-radius:50%;background:var(--blue)}

/* features */
.features{left:111px;top:2609px;width:978px;height:283px;background:var(--white);border-radius:12px;box-shadow:0 0 10px rgba(0,0,0,.12)}
.feature{position:absolute;top:0;height:283px;text-align:center}
.feature svg{position:absolute;left:50%;top:32px;transform:translateX(-50%)}
.feature h3{position:absolute;left:0;width:100%;top:127px;font-size:18px;font-weight:400;text-transform:uppercase;color:var(--ink)}
.feature p{position:absolute;left:0;width:100%;top:167px;font-size:14px;line-height:32.5px;color:var(--muted)}
.divider{position:absolute;top:18px;width:1px;height:247px;background:#e3e5ea}

/* news */
.news-card{position:absolute;top:3054px;width:468px;height:219px;border-radius:12px;background:var(--white);box-shadow:0 0 8px rgba(0,0,0,.12);overflow:hidden}
.news-card .img{position:absolute;left:8px;top:12px;width:170px;height:196px;border-radius:10px}
.news-card .date{position:absolute;left:212px;top:34px;font-size:11.5px;text-transform:uppercase;display:flex;align-items:center;gap:10px}
.news-card h3{position:absolute;left:212px;top:64px;width:240px;font-size:14.5px;font-weight:500;line-height:32px;color:var(--blue);text-transform:uppercase}
.news-card p{position:absolute;left:212px;top:138px;width:245px;font-size:12.5px;line-height:28px;color:var(--muted)}
.news-card .go{position:absolute;right:0;bottom:0;width:42px;height:36px;background:var(--blue);border-top-left-radius:36px}

/* newsletter */
.loop{left:0;top:3450px;width:1200px;height:109px;background:var(--blue)}
.loop h2{position:absolute;left:110px;top:38px;font-size:26px;font-weight:600;color:var(--white);text-transform:uppercase;letter-spacing:-.3px}
.loop .field{position:absolute;left:708px;top:35px;width:375px;height:41px;border-radius:22px;background:#3f7cc6}
.loop .field span{position:absolute;left:26px;top:13px;font-size:10.5px;color:#9dbbe3;text-transform:uppercase}
.loop .field .pill{left:226px;top:4px;width:146px;height:33px;background:var(--white);color:var(--ink);font-size:11.5px}

/* footer */
.footer{left:0;top:3559px;width:1200px;height:365px;background:var(--dark)}
.footer .brand{left:101px;top:60px;z-index:1}
.footer h4{position:absolute;top:56px;font-size:18px;font-weight:500;color:var(--sky);text-transform:uppercase}
.footer .links a{position:absolute;font-size:12px;color:var(--white);text-decoration:none;text-transform:uppercase}
.footer .contact{position:absolute;left:839px;display:flex;align-items:center;gap:22px;font-size:12.5px;color:var(--white);line-height:30px;text-transform:uppercase}
.footer .contact i{display:flex;align-items:center;justify-content:center;width:36px;height:36px;border-radius:50%;background:var(--blue);flex:none}
.footer .rule{position:absolute;left:111px;top:305px;width:978px;height:1px;background:#2e3035}
.footer .copy{position:absolute;left:111px;top:327px;font-size:12.5px;color:var(--white);text-transform:uppercase}
.footer .copy span{color:var(--sky)}
.social{position:absolute;top:321px;width:26px;height:26px;border-radius:50%;border:1.5px solid var(--white)}
</style>
</head>
<body>

<!-- header -->
<div class="abs topbar"></div>
<div class="abs brand"><span>Calloway Food Hall</span></div>
<nav class="nav">
  <a class="active" style="left:469px" href="#">Home</a>
  <a style="left:535px" href="#">About Us</a>
  <a style="left:627px" href="#">Vendors &#9662;</a>
  <a style="left:716px" href="#">Latest News</a>
  <a style="left:835px" href="#">Contact Us</a>
</nav>
<a class="pill solid" style="left:970px;top:18px;width:117px;height:33px;font-size:11.5px" href="#">Get Started</a>

<section class="abs hero" role="img" aria-label="Couple walking through a bright food hall with counters and seating"></section>
<div class="abs hero-kicker">Coming Summer 2025</div>
<h1 class="abs hero-title">Savor the Coast.<br>Taste San Clemente.</h1>
<p class="abs hero-copy">Lorem ipsum dolor sit amet, consectetur adipiscing elit, sed do eiusmod tempor incididunt ut labore et dolore magna aliqua enim ad minim veniam.</p>
<a class="pill solid" style="left:111px;top:472px;width:165px;height:41px" href="#">Explore Vendors</a>
<a class="pill sky" style="left:289px;top:472px;width:191px;height:41px" href="#">Join Our Mailing List</a>

<!-- about -->
<section class="abs about"></section>
<div class="photo" style="left:113px;top:647px;width:225px;height:250px;background:linear-gradient(160deg,#e7e9ec,#6f6a66 70%,#3a3a40)" role="img" aria-label="Friends chatting at a table in the food hall"></div>
<div class="photo" style="left:352px;top:688px;width:208px;height:208px;background:linear-gradient(160deg,#8a5a3a,#c9a98a 55%,#4b3a30)" role="img" aria-label="Crowded communal tables with diners"></div>
<div class="photo" style="left:129px;top:911px;width:209px;height:208px;background:linear-gradient(160deg,#c97b3d,#e3c7a5 45%,#6a4c3a)" role="img" aria-label="Family sharing plates of food"></div>
<div class="photo" style="left:352px;top:911px;width:225px;height:250px;background:linear-gradient(180deg,#2f3a3e,#4f6a6a 50%,#8a6a48)" role="img" aria-label="Overhead view of market hall with long wooden tables"></div>
<h2 class="section-title" style="left:659px;top:640px">About <span>Calloway Food Hall</span></h2>
<div class="abs body-copy" style="left:659px;top:697px;width:440px">
  <p>Lorem ipsum dolor sit amet, consectetur adipiscing elit, sed do eiusmod tempor incididunt ut labore et dolore magna aliqua. Ut enim ad minim veniam, quis nostrud exercitation ullamco laboris nisi ut aliquip ex ea commodo consequat. Duis aute irure dolor in reprehenderit in voluptate velit esse cillum dolore eu fugiat nulla pariatur.</p>
  <p style="margin-top:15px">Lorem ipsum dolor sit amet, consectetur adipiscing elit, sed do eiusmod tempor incididunt ut labore et dolore magna aliqua enim ad minim veniam.</p>
  <p style="margin-top:15px;width:400px">Lorem ipsum dolor sit amet, consectetur adipiscing elit sed do eiusmod tempor incididunt</p>
</div>
<a class="pill solid" style="left:659px;top:1110px;width:139px;height:44px" href="#">Learn More</a>

<!-- vendors -->
<h2 class="section-title" style="left:0;width:1200px;text-align:center;top:1314px">Explore <span>Our Vendors</span></h2>
<svg class="abs" style="left:47px;top:1506px" width="16" height="22" viewBox="0 0 16 22"><path d="M12 3 4 11l8 8" fill="none" stroke="#111" stroke-width="2.5"/></svg>
<svg class="abs" style="left:1132px;top:1506px" width="16" height="22" viewBox="0 0 16 22"><path d="m4 3 8 8-8 8" fill="none" stroke="#111" stroke-width="2.5"/></svg>

<div class="vendor-card" style="left:111px">
  <div class="img" style="background:linear-gradient(180deg,#7fb8dc,#bcd7e0 45%,#d9a95a 80%,#8a6a3a)" role="img" aria-label="Tacos on a beach with palm trees"></div>
  <h3>Tide Line Tacos</h3>
  <p>Modern coastal tacos with bold Baja flavors.</p>
  <a class="pill line" href="#">Visit Website</a>
</div>
<div class="vendor-card featured" style="left:445px">
  <div class="img" style="background:linear-gradient(180deg,#9fc8ea,#d7dde2 50%,#5c7a4c)" role="img" aria-label="Thai restaurant storefront with plants"></div>
  <h3>Coastline Thai</h3>
  <p>Authentic Thai dishes with a SoCal twist.</p>
  <a class="pill line" href="#">Visit Website</a>
</div>
<div class="vendor-card" style="left:777px">
  <div class="img" style="background:linear-gradient(160deg,#c93a3a,#e88a84 55%,#3a2a2a)" role="img" aria-label="Pizza shop counter with red wall"></div>
  <h3>Harbor Pizza Co</h3>
  <p>Wood-fired pizzas made with fresh, local ingredients.</p>
  <a class="pill line" href="#">Visit Website</a>
</div>

<!-- become a vendor -->
<section class="abs become"></section>
<h2 class="section-title" style="left:111px;top:1982px">Become <span>A Vendor</span></h2>
<p class="abs body-copy" style="left:111px;top:2041px;width:440px">Are you a local chef, food brand, or beverage concept ready to serve the vibrant community of San Clemente? Join the hand-picked lineup of Calloway Food Hall vendors and be part of something fresh, local, and unforgettable.</p>
<ul class="abs perks">
  <li>Prime location by the Pacific Ocean</li>
  <li>Built-in foot traffic from locals &amp; tourists</li>
  <li>Marketing support from our team</li>
  <li>A community-first food culture</li>
  <li>Flexible vendor spaces &amp; lease options</li>
</ul>
<p class="abs body-copy" style="left:111px;top:2386px;width:430px">We're opening Summer 2025 — don't miss the opportunity to get in early.</p>
<a class="pill solid" style="left:111px;top:2482px;width:139px;height:42px" href="#">Read More</a>
<div class="abs" style="left:646px;top:1994px;width:443px;height:530px;border-radius:16px;background:var(--sky)"></div>
<div class="abs" style="left:651px;top:1999px;width:438px;height:525px;border-radius:14px;background:linear-gradient(170deg,#d9c7a8,#7a3f55 35%,#c9d48a 55%,#b8434a 75%,#e6dccb)" role="img" aria-label="Sushi burrito cut in half showing tuna, greens and rice"></div>

<!-- features -->
<div class="abs features">
  <div class="feature" style="left:0;width:311px">
    <svg width="66" height="66" viewBox="0 0 66 66" fill="none" stroke="#0a56b0" stroke-width="2.2"><rect x="6" y="4" width="22" height="18" rx="3"/><rect x="38" y="4" width="22" height="18" rx="3"/><path d="m11 13 4 4 8-8"/><circle cx="17" cy="40" r="9"/><circle cx="49" cy="40" r="9"/><rect x="4" y="52" width="58" height="8" rx="4"/></svg>
    <h3>Quality Food</h3>
    <p>Lorem ipsum dolor sit amet,<br>consectetur adipiscing elit, sed do<br>eiusmod tempor incididunt</p>
  </div>
  <div class="divider" style="left:311px"></div>
  <div class="feature" style="left:311px;width:359px">
    <svg width="70" height="66" viewBox="0 0 70 66" fill="none" stroke="#0a56b0" stroke-width="2.2"><circle cx="35" cy="22" r="18"/><path d="M28 24v8h14l3-10h-9l1-8-4 0-5 10z"/><path d="M4 46h62l-6 14H10z"/><path d="M4 46c6-6 12-6 18 0m4 0c6-6 12-6 18 0m4 0c6-6 12-6 18 0"/></svg>
    <h3>100% Organic Guarantee</h3>
    <p>Lorem ipsum dolor sit amet,<br>consectetur adipiscing elit, sed do<br>eiusmod tempor incididunt</p>
  </div>
  <div class="divider" style="left:670px"></div>
  <div class="feature" style="left:670px;width:308px">
    <svg width="66" height="66" viewBox="0 0 66 66" fill="none" stroke="#0a56b0" stroke-width="2.2"><rect x="38" y="6" width="22" height="20" rx="2"/><circle cx="34" cy="10" r="5"/><path d="M32 18l-8 14 10 6-6 20m6-20 10 12"/><path d="M4 26h16M8 34h14M4 42h16"/></svg>
    <h3>Fast Delivery</h3>
    <p>Lorem ipsum dolor sit amet,<br>consectetur adipiscing elit, sed do<br>eiusmod tempor incididunt</p>
  </div>
</div>

<!-- news -->
<h2 class="section-title" style="left:0;width:1200px;text-align:center;top:2968px"><span style="color:var(--navy)">Latest</span> <span>News</span></h2>
<article class="news-card" style="left:111px">
  <div class="img" style="background:linear-gradient(180deg,#cfd4d8,#8c7f6c 55%,#b8553a)" role="img" aria-label="Market hall interior with produce stands"></div>
  <div class="date"><svg width="12" height="12" viewBox="0 0 12 12"><rect x="1" y="2" width="10" height="9" fill="#0a56b0"/></svg>Posted April 21, 2025</div>
  <h3>Grand Opening Set for Summer 2025</h3>
  <p>We're getting ready to open our doors just steps from the Pacific!</p>
  <span class="go"><svg class="abs" style="left:18px;top:12px" width="10" height="14" viewBox="0 0 10 14"><path d="m2 2 5 5-5 5" fill="none" stroke="#fff" stroke-width="2"/></svg></span>
</article>
<article class="news-card" style="left:623px">
  <div class="img" style="background:linear-gradient(160deg,#3a2a22,#a8643a 50%,#d9b07a)" role="img" aria-label="Chefs at a busy food counter"></div>
  <div class="date"><svg width="12" height="12" viewBox="0 0 12 12"><rect x="1" y="2" width="10" height="9" fill="#0a56b0"/></svg>Posted April 10, 2025</div>
  <h3>Vendor Spotlight: Harbor Pizza Co.</h3>
  <p>Get to know one of our featured vendors bringing handcrafted</p>
  <span class="go"><svg class="abs" style="left:18px;top:12px" width="10" height="14" viewBox="0 0 10 14"><path d="m2 2 5 5-5 5" fill="none" stroke="#fff" stroke-width="2"/></svg></span>
</article>
<a class="pill solid" style="left:509px;top:3325px;width:181px;height:42px" href="#">View More News</a>

<!-- newsletter -->
<section class="abs loop">
  <h2>Stay in the Loop</h2>
  <div class="field"><span>Email Address</span><a class="pill" href="#">Subscribe Now</a></div>
</section>

<!-- footer -->
<footer class="abs footer">
  <div class="abs brand"><span>Calloway Food Hall</span></div>
  <h4 style="left:358px">Quick Links</h4>
  <h4 style="left:595px">Other Links</h4>
  <h4 style="left:839px">Contact Us</h4>
  <div class="links">
    <a style="left:358px;top:104px" href="#">Home</a>
    <a style="left:358px;top:137px" href="#">About Us</a>
    <a style="left:358px;top:169px" href="#">Vendors</a>
    <a style="left:358px;top:202px" href="#">Latest News</a>
    <a style="left:358px;top:234px" href="#">Contact Us</a>
    <a style="left:595px;top:104px" href="#">Privacy Policy</a>
    <a style="left:595px;top:137px" href="#">Terms of Use</a>
    <a style="left:595px;top:169px" href="#">Site Map</a>
    <a style="left:595px;top:202px" href="#">Cookies</a>
  </div>
  <div class="contact" style="top:104px"><i><svg width="14" height="14" viewBox="0 0 14 14"><path d="M3 1l2 3-1 2a8 8 0 0 0 4 4l2-1 3 2-1 2C6 13 1 8 1 3z" fill="#fff"/></svg></i>+1 555 010 2025</div>
  <div class="contact" style="top:160px"><i><svg width="14" height="12" viewBox="0 0 14 12"><rect x="1" y="2" width="12" height="8" fill="#fff"/><path d="m1 2 6 5 6-5" fill="none" stroke="#0a56b0" stroke-width="1.2"/></svg></i>Info@callowayfoodhall.com</div>
  <div class="contact" style="top:206px"><i><svg width="12" height="16" viewBox="0 0 12 16"><path d="M6 1a5 5 0 0 1 5 5c0 4-5 9-5 9S1 10 1 6a5 5 0 0 1 5-5z" fill="#fff"/><circle cx="6" cy="6" r="2" fill="#0a56b0"/></svg></i><span>1450 Seabreeze Avenue<br>San Clemente, CA 92672</span></div>
  <div class="rule"></div>
  <p class="copy">©2025 <span>Calloway Food Hall</span> Copyrights - All Rights Reserved</p>
  <span class="social" style="left:967px"></span>
  <span class="social" style="left:998px"></span>
  <span class="social" style="left:1029px"></span>
  <span class="social" style="left:1060px"></span>
</footer>

</body>
</html>
```